Young, dynamic furniture company needs a new business card design

We require a new business card design for our modern furniture company which supplies furniture and appliances to the property and development market.
Oakridge Interiors has become one of the leading furniture & appliance suppliers to the property market withing London. With over 10 years experience, we have increased our business to supply not only private landlords and managing agents, but also property developers, housing associations and local councils.
We offer not only a complete range of furniture which includes beds, wardrobes, dining sets and sofas, but also a high quality, full delivery and assembly service to help you with all our furnishing needs.

Target Market(s)

Private landlords, estate agents, letting agents, property management companies

Industry/Entity Type

Business

Contact Information for Business Card

Name,
Title,
Address,
Mobile,
Telephone,
Fax, Website, email address

Font styles to use
Sans Serif

Colors
3176b5
0555a3
85abd2
cfdeed

Requirements
Must have
• All the above information for each of our staff, along with our logo

```html
<!DOCTYPE html>
<html lang="en">
<head>
<meta charset="utf-8">
<title>Oakridge Interiors – Business Card</title>
<link rel="stylesheet" href="https://fonts.googleapis.com/css2?family=Lato:wght@300;400;700&display=swap">
<style>
  :root {
    --blue: #3176b5;
    --deep-blue: #0555a3;
    --soft-blue: #85abd2;
    --pale-blue: #cfdeed;
    --ink: #1b1b1b;
    --white: #ffffff;
    --backdrop: #e9edf2;
  }
  * { margin: 0; padding: 0; box-sizing: border-box; }
  html, body { width: 1200px; height: 900px; overflow: hidden; }
  body {
    background: var(--backdrop);
    font-family: "Lato", sans-serif;
    position: relative;
  }
  .card {
    position: absolute;
    width: 620px;
    height: 354px;
    overflow: hidden;
    box-shadow: 0 10px 28px rgba(20, 40, 70, 0.22);
  }
  .card-back { left: 500px; top: 70px; background: var(--deep-blue); color: var(--white); }
  .card-front { left: 80px; top: 470px; background: var(--white); }

  .card-bg { position: absolute; inset: 0; width: 100%; height: 100%; }

  /* Brand lockup */
  .brand { display: flex; align-items: center; gap: 12px; }
  .brand-square { width: 22px; height: 22px; background: var(--blue); flex: none; }
  .brand-name {
    font-weight: 400;
    font-size: 28px;
    letter-spacing: 1px;
    text-transform: uppercase;
    line-height: 1;
  }
  .brand-tagline {
    font-weight: 400;
    font-size: 11px;
    letter-spacing: 1.2px;
    text-transform: uppercase;
    margin-top: 6px;
  }

  /* Back */
  .card-back .brand-block {
    position: absolute; left: 0; right: 0; top: 120px;
    display: flex; flex-direction: column; align-items: center;
  }
  .card-back .brand-square { background: var(--white); }
  .card-back .brand-name { color: var(--white); }
  .card-back .brand-tagline { color: var(--pale-blue); }
  .card-back .website {
    margin-top: 28px;
    font-size: 15px;
    letter-spacing: 2.5px;
  }

  /* Front */
  .card-front .brand-block { position: absolute; left: 40px; top: 56px; }
  .card-front .brand-name { color: var(--ink); }
  .card-front .brand-tagline { color: var(--ink); margin-left: 34px; }

  .address {
    position: absolute; left: 40px; top: 244px;
    color: var(--white); font-size: 17px; line-height: 24px;
    font-style: normal;
  }
  .contact {
    position: absolute; right: 36px; top: 192px;
    color: var(--white); text-align: right;
  }
  .person-name { font-size: 27px; font-weight: 400; line-height: 1.1; }
  .person-title { font-size: 18px; line-height: 22px; margin-bottom: 6px; }
  .contact-list { list-style: none; font-size: 17px; line-height: 22px; }
  .contact-list li { display: flex; justify-content: flex-end; align-items: center; gap: 10px; }
  .icon { width: 15px; height: 15px; flex: none; }
</style>
</head>
<body>

<section class="card card-back" aria-label="Business card back">
  <div class="brand-block">
    <div class="brand">
      <span class="brand-square"></span>
      <span class="brand-name">Oakridge Interiors</span>
    </div>
    <div class="brand-tagline">Trade Furniture Solutions</div>
    <div class="website">www.oakridge-trade.co.uk</div>
  </div>
</section>

<section class="card card-front" aria-label="Business card front">
  <svg class="card-bg" viewBox="0 0 620 354" preserveAspectRatio="none" aria-hidden="true">
    <path class="band" d="M0,170 Q300,306 620,60 L620,354 L0,354 Z" fill="var(--blue)"/>
    <path class="swoosh" d="M0,170 Q300,290 620,38 L620,50 Q300,300 0,170 Z" fill="var(--soft-blue)"/>
  </svg>

  <div class="brand-block">
    <div class="brand">
      <span class="brand-square"></span>
      <span class="brand-name">Oakridge Interiors</span>
    </div>
    <div class="brand-tagline">Trade Furniture Solutions</div>
  </div>

  <address class="address">
    14C Millbrook Industrial Park<br>
    Northfield Green, London
  </address>

  <div class="contact">
    <div class="person-name">Daniel Hartley</div>
    <div class="person-title">Manager</div>
    <ul class="contact-list">
      <li>020 7946 0321
        <svg class="icon" viewBox="0 0 16 16" aria-hidden="true"><path d="M3.5 1.5l2.5 0 1 3.5-1.6 1.2a8 8 0 0 0 4.4 4.4l1.2-1.6 3.5 1v2.5c0 .8-.7 1.5-1.5 1.5A11.5 11.5 0 0 1 2 3c0-.8.7-1.5 1.5-1.5z" fill="var(--white)"/></svg>
      </li>
      <li>020 7946 0800
        <svg class="icon" viewBox="0 0 16 16" aria-hidden="true"><rect x="4" y="1" width="8" height="14" rx="1.5" fill="none" stroke="var(--white)" stroke-width="1.5"/><rect x="6" y="3.5" width="4" height="5" fill="var(--white)"/><circle cx="8" cy="12.3" r="1" fill="var(--white)"/></svg>
      </li>
      <li>info@oakridge-trade.co.uk
        <svg class="icon" viewBox="0 0 16 16" aria-hidden="true"><rect x="1" y="3" width="14" height="10" fill="var(--white)"/><path d="M1 3l7 6 7-6" fill="none" stroke="var(--blue)" stroke-width="1.3"/></svg>
      </li>
      <li>www.oakridge-trade.co.uk
        <svg class="icon" viewBox="0 0 16 16" aria-hidden="true"><circle cx="8" cy="8" r="7" fill="var(--white)"/><g fill="none" stroke="var(--blue)" stroke-width="1"><ellipse cx="8" cy="8" rx="3" ry="7"/><path d="M1 8h14M2.5 4.5h11M2.5 11.5h11"/></g></svg>
      </li>
    </ul>
  </div>
</section>

</body>
</html>
```